New Business Card Design Project

I need a design for business cards, i am an electrical business called "Corvane Electrical and Communications" i need the cards to be double sided with the company logo on the back (attached) the front needs to say my company name, web site, email address, telephone number, and ABN number and electrical license number. I am open to different arrangements of the information but would like the background to be incorporating something electrical or something that looks smart. open to all additional ideas also.

The company colours are orange and grey see logo attached.

Business Name: Corvane Electrical and Communications
Website: corvaneelectricalandcomms.example.com.au
Email: brent@corvaneelectricalandcomms.example.com.au
Telephone(mobile): 0481209736
ABN: 71208349162
Lic No: 418273D

Target Market(s)

Business entities, Project Managers, Accounts, Clients

Industry/Entity Type

Electrician

Contact Information for Business Card

I need a design for business cards, i am an electrical business called "Corvane Electrical and Communications" i need the cards to be double sided with the company logo on the back (attached) the front needs to say my company name

Font styles to use
Serif
Sans Serif

Colors
f37122
5c5c5c

Requirements
Must have
• Must have the Logo on the back open to different ways of it being on the back but had in mind to keep it central but again open to other options
Nice to have
• A real modern cool background that is eye catching yet contemporary
Should not have
• No backgrounds of a light bulb or plug or anything like that

```html
<!DOCTYPE html>
<html lang="en">
<head>
<meta charset="utf-8">
<title>Corvane Electrical and Communications – Business Card</title>
<link rel="stylesheet" href="https://fonts.googleapis.com/css2?family=Exo+2:wght@300;400;600&display=swap">
<style>
  :root {
    --brand-orange: #f37122;
    --brand-orange-deep: #c5551a;
    --brand-grey: #5c5c5c;
    --card-dark: #1f1f20;
    --card-mid: #3b3b3d;
    --text-light: #d8d8d8;
    --text-soft: #bdbdbd;
    --backdrop: #e7e3de;
  }
  * { box-sizing: border-box; margin: 0; padding: 0; }
  html, body {
    width: 1200px; height: 969px; overflow: hidden;
    background: var(--backdrop);
    font-family: "Exo 2", Arial, sans-serif;
  }
  .canvas { position: relative; width: 1200px; height: 969px; }
  .business-card {
    position: absolute; left: 100px; top: 201px;
    width: 1000px; height: 567px;
    border-radius: 26px; overflow: hidden;
    box-shadow: 0 18px 40px rgba(0,0,0,.25);
    background: linear-gradient(135deg, var(--card-mid) 0%, var(--card-dark) 55%, #161617 100%);
  }
  .accent-panel {
    position: absolute; top: 0; right: 0;
    width: 300px; height: 100%;
    background: linear-gradient(45deg, var(--brand-orange) 0%, #e0681f 60%, var(--brand-orange-deep) 100%);
  }
  .brand-name {
    position: absolute; left: 65px; top: 122px;
    color: var(--text-light); font-weight: 300;
    text-transform: uppercase; line-height: 1;
  }
  .brand-name .word { display: block; font-size: 64px; letter-spacing: 4px; }
  .brand-name .sub { display: block; font-size: 17px; letter-spacing: 1.6px; margin-top: 12px; }
  .registration {
    position: absolute; left: 57px; top: 318px;
    color: var(--text-soft); font-size: 24px; line-height: 38px;
  }
  .contact-list {
    position: absolute; left: 57px; top: 406px; list-style: none;
    color: var(--text-soft);
  }
  .contact-list li { display: flex; align-items: center; height: 40px; }
  .contact-list .icon { width: 24px; height: 24px; margin-right: 14px; flex: none; }
  .contact-list .phone { font-size: 25px; }
  .contact-list .email, .contact-list .web { font-size: 19px; }
  .person {
    position: absolute; left: 885px; top: 300px;
    transform: translate(-50%, -50%) rotate(-90deg);
    white-space: nowrap; line-height: 1.15;
  }
  .person .name { display: block; font-size: 32px; font-weight: 600; color: var(--text-light); }
  .person .role { display: block; font-size: 24px; font-weight: 400; color: var(--brand-grey); }
</style>
</head>
<body>
<main class="canvas">
  <section class="business-card">
    <div class="accent-panel" role="img" aria-label="Orange panel with a hanging power cord illustration"></div>

    <h1 class="brand-name">
      <span class="word">Corvane</span>
      <span class="sub">Electrical &amp; Communications</span>
    </h1>

    <p class="registration">
      ABN: 71208349162<br>
      Lic No: 418273D
    </p>

    <ul class="contact-list">
      <li class="phone">
        <svg class="icon" viewBox="0 0 24 24"><rect x="6" y="2" width="12" height="20" rx="2" fill="none" stroke="var(--brand-orange)" stroke-width="2.4"/><rect x="10" y="17" width="4" height="2" fill="var(--brand-orange)"/></svg>
        0481209736
      </li>
      <li class="email">
        <svg class="icon" viewBox="0 0 24 24"><rect x="2" y="5" width="20" height="14" rx="1.5" fill="var(--brand-orange)"/><path d="M3 6 L12 13 L21 6" fill="none" stroke="#2a2a2a" stroke-width="1.8"/></svg>
        brent@corvaneelectricalandcomms.example.com.au
      </li>
      <li class="web">
        <svg class="icon" viewBox="0 0 24 24"><circle cx="12" cy="12" r="10" fill="var(--brand-orange)"/><path d="M2 12 H22 M12 2 C7 7 7 17 12 22 M12 2 C17 7 17 17 12 22" fill="none" stroke="#2a2a2a" stroke-width="1.4"/></svg>
        corvaneelectricalandcomms.example.com.au
      </li>
    </ul>

    <p class="person">
      <span class="name">Brent Marlow</span>
      <span class="role">CEO/Founder</span>
    </p>
  </section>
</main>
</body>
</html>
```